Business card for law firm

Need business card for new law firm. Think confident, authoritative, conservative, but not stuffy or old-fashioned.

Contact Information for Business Card

Content for card - logo (uploaded), plus the following:

Paul Whitcombe (larger font)
Managing Partner (larger font, but not as large as name)
Level 9, 7 Ferris Lane
Sydney NSW 2000
Main Tel 02 9364 2710
Direct Tel 02 8472 3159
Email paul@qvlegal.com.au
www.qvlegal.com.au

Letterhead design should include logo plus:
Level 9, 7 Ferris Lane
Sydney NSW 2000
Tel 02 8472 3159
www.qvlegal.com.au

```html
<!DOCTYPE html>
<html lang="en">
<head>
<meta charset="utf-8">
<title>QV Legal Letterhead</title>
<link href="https://fonts.googleapis.com/css2?family=Lato:wght@400&display=swap" rel="stylesheet">
<style>
  :root {
    --navy: #1c2255;
    --ink: #1a1a1a;
    --paper: #ffffff;
  }
  html, body {
    margin: 0;
    padding: 0;
    overflow: hidden;
    background: var(--paper);
  }
  .letterhead {
    position: relative;
    width: 1200px;
    height: 1200px;
    background: var(--paper);
    overflow: hidden;
    font-family: "Lato", Arial, sans-serif;
  }
  .brand {
    position: absolute;
    top: 52px;
    left: 0;
    width: 100%;
    display: flex;
    flex-direction: column;
    align-items: center;
  }
  .brand-mark {
    width: 54px;
    height: 54px;
    background: var(--navy);
  }
  .brand-name {
    margin-top: 30px;
    font-size: 40px;
    font-weight: 400;
    letter-spacing: 4px;
    color: var(--ink);
    line-height: 1;
  }
  .footer-address {
    position: absolute;
    top: 1153px;
    left: 0;
    width: 100%;
    text-align: center;
    font-size: 14.5px;
    color: var(--ink);
    margin: 0;
  }
  .footer-address .divider {
    margin: 0 6px;
  }
  .footer-bar {
    position: absolute;
    left: 429px;
    top: 1188px;
    width: 305px;
    height: 12px;
    background: var(--navy);
  }
</style>
</head>
<body>
  <main class="letterhead">
    <header class="brand">
      <div class="brand-mark"></div>
      <div class="brand-name">QV LEGAL</div>
    </header>
    <p class="footer-address">Level 9, 7 Ferris Lane, Sydney NSW 2000. Tel: 02 8472 3159<span class="divider">|</span>www.qvlegal.com.au</p>
    <div class="footer-bar"></div>
  </main>
</body>
</html>
```